Cutting Edge Property Services Provider is Looking to Update Business Card Design

We are looking to freshen up our business cards to match our cutting edge technology based image.

KORVANEX - Where Care Finds Its Pulse

More information about our company can be found on our website at www.korvanex-demo.net

We integrate technology in a historically low tech industry.

We have appeared on the Brisk 300/3000 list 2 years in a row and we're previously recognized as the 5th Quickest Rising Firm in San Diego.

Our core colors are blue and white, but are not against accents that might improve our image.

We currently have our Mission Statement on our Business Cards in a folding design:
KORVANEX IS THE LEADING BUILDING SERVICES INNOVATOR. BY COMBINING TECHNOLOGY WITH FUNCTIONAL TOOS THAT IMPROVE EFFICIENCY IN THE WORKPLACE, WE PROVIDE UNPARALLELED SERVICE IN THE INDUSTRY. DEVELOPING LASTING RELATIONSHIPS WITH OUR CLIENTS AND ASSOCIATES IS THE CORNERSTONE OF OUR SUCCESS.

We'd like to convey the image of a cutting edge, technology based company. Want the cards to pop.

Target Market(s)

Commercial Property Managers - 20 to 50 year old professionals

Industry/Entity Type

Business

Requirements
Must have
• Must utilize our logo obviously, but are definitely open to using variations on the logo. Utilizing the components of the logo, but maybe in different configurations or backgrounds, etc...

Must use the Name: KORVANEX.
Can also use KORVANEX PROPERTY SERVICES.

Must include the Mission Statement

Must say: Where Care Finds Its Pulse
Nice to have
• We are considering plastic stock, shaped cards, or folding cards.

Nothing over the top or really expensive, but will consider if it conveys innovation and technology.
Should not have
• No images of toilets, buildings, trees, or anything relating to commercial properties.

We want to convey our technology image.

```html
<!DOCTYPE html>
<html lang="en">
<head>
<meta charset="utf-8">
<title>Korvanex Business Card – Front and Back</title>
<link rel="stylesheet" href="https://fonts.googleapis.com/css2?family=Jost:wght@400;500;700&display=swap">
<style>
  :root {
    --brand-blue: #0b4a7d;
    --brand-blue-deep: #083a63;
    --card-frost: #e9edf1;
    --card-edge: #d5dce3;
    --swoosh-white: #ffffff;
    --swoosh-grey: #b9c0c7;
    --text-on-blue: #ffffff;
    --page-bg: #f3f4f6;
  }
  * { box-sizing: border-box; margin: 0; padding: 0; }
  html, body {
    width: 1200px; height: 900px; overflow: hidden;
    background: var(--page-bg);
    font-family: "Jost", "Futura", sans-serif;
  }
  .canvas { position: relative; width: 1200px; height: 900px; }

  .card {
    position: absolute; left: 322px;
    width: 556px; height: 316px;
    border-radius: 18px; overflow: hidden;
    background: var(--card-frost);
    box-shadow: 0 6px 22px rgba(20, 40, 70, 0.14);
    border: 1px solid var(--card-edge);
  }
  .card--front { top: 100px; }
  .card--back  { top: 484px; }
  .card__art { position: absolute; inset: 0; width: 100%; height: 100%; }

  .brand {
    position: absolute; left: 46px; top: 60px;
    display: flex; align-items: center; gap: 12px;
    color: var(--brand-blue); font-weight: 700;
    font-size: 34px; letter-spacing: 1px;
  }
  .brand__mark { width: 22px; height: 22px; background: var(--brand-blue); }

  .tagline {
    position: absolute; right: 32px; top: 32px;
    text-align: right; color: var(--brand-blue);
    font-size: 19px; line-height: 24px;
  }

  .person { position: absolute; left: 42px; top: 212px; color: var(--text-on-blue); }
  .person__name { font-size: 18px; line-height: 22px; }
  .person__role { font-size: 13px; line-height: 18px; }
  .person__phones { position: absolute; left: 42px; top: 268px; color: var(--text-on-blue); font-size: 15px; line-height: 20px; }

  .contact { position: absolute; right: 28px; color: var(--text-on-blue); text-align: right; font-size: 14.5px; line-height: 23px; }
  .contact--online { top: 197px; }
  .contact--address { top: 264px; line-height: 19px; }

  .mission {
    position: absolute; left: 36px; right: 36px; top: 206px;
    color: var(--text-on-blue); text-align: center;
    font-size: 14.5px; line-height: 18px;
  }
</style>
</head>
<body>
<main class="canvas">

  <section class="card card--front" aria-label="Business card front">
    <svg class="card__art" viewBox="0 0 556 316" aria-hidden="true">
      <path d="M0,198 C170,190 360,160 556,122 L556,316 L0,316 Z" fill="var(--brand-blue)"/>
      <path d="M0,172 C150,192 330,168 556,124" fill="none" stroke="var(--swoosh-white)" stroke-width="10"/>
      <path d="M0,188 C160,205 350,176 556,132" fill="none" stroke="var(--swoosh-grey)" stroke-width="4"/>
    </svg>

    <div class="brand"><span class="brand__mark"></span><span class="brand__name">KORVANEX</span></div>
    <p class="tagline">Where Care<br>Finds Its Pulse</p>

    <div class="person">
      <p class="person__name">Your Name</p>
      <p class="person__role">Designation</p>
    </div>
    <p class="person__phones">cell : +12 345 67 8910<br>phone : +12 345 67 8910</p>

    <p class="contact contact--online">email : info@korvanex-demo.net<br>web : www.korvanex-demo.net</p>
    <p class="contact contact--address">123, Abc Street<br>0000 City, Country</p>
  </section>

  <section class="card card--back" aria-label="Business card back">
    <svg class="card__art" viewBox="0 0 556 316" aria-hidden="true">
      <path d="M0,124 C190,160 380,192 556,200 L556,316 L0,316 Z" fill="var(--brand-blue)"/>
      <path d="M0,126 C200,168 400,194 556,174" fill="none" stroke="var(--swoosh-white)" stroke-width="10"/>
      <path d="M0,134 C200,180 400,206 556,188" fill="none" stroke="var(--swoosh-grey)" stroke-width="4"/>
    </svg>

    <p class="mission">Korvanex is the leading building services innovator. By combining technology with functional toos that improve efficiency in the workplace, we provide unparalleled service in the industry. Developing lasting relationships with our clients and associates is the cornerstone of our success.</p>
  </section>

</main>
</body>
</html>
```